Vennekamp.dk - FellowCup

I need a design for a WordPress site that serves to inform and present the national golfchampionship for colleagues in Denmark. The sites need to be visual stuninng or big, and it doesnt have a lot of pages. Maybe 5-6 regular text pages and not a lot of navigation. It should be a simple and powerfull site.

The sites need to present and sell the tournament, and have a clear call to action button "Sign up" (Tilmeld) and resultscoring.

If you can make a logo and visual ID for the tournament as well that would be a bonus.

Target Market(s)

Golfers

Logo Text

Vennekamp

Number of Pages Required

3 page

Requirements
Must have
• A frontpage
• Button 1 - Tilmeld (danish for sign up)
• Button 2 - Resultater (results)
Nice to have
• Logo
• A style we can use offline as well

```html
<!DOCTYPE html>
<html lang="da">
<head>
<meta charset="utf-8">
<title>Vennekamp.dk – FellowCup</title>
<link href="https://fonts.googleapis.com/css2?family=Open+Sans:wght@400;600;700&display=swap" rel="stylesheet">
<style>
:root{
  --green:#1ea85a;--yellow:#f2b705;--yellow-dark:#e5a800;--blue:#1a8ed1;--red:#e02834;
  --text:#333;--muted:#666;--line:#e4e4e4;--gray:#efefef;--dark:#2b2b2b;
}
*{box-sizing:border-box;margin:0;padding:0}
html,body{width:707px;height:1200px;overflow:hidden}
body{position:relative;background:#fff;font-family:'Open Sans',sans-serif;color:var(--text)}
.abs{position:absolute}
.topbar{left:0;top:0;width:707px;height:2px;background:linear-gradient(90deg,var(--red) 0 25%,var(--yellow) 25% 50%,var(--green) 50% 75%,var(--blue) 75%)}
.brand{left:96px;top:18px;display:flex;align-items:center;gap:7px}
.brand-dot{width:30px;height:30px;border-radius:50%;background:var(--blue)}
.brand-name{font-size:8px;font-weight:600;line-height:9px;letter-spacing:1px;color:#1d3557;text-transform:uppercase;width:90px}
.search{left:416px;top:22px;width:98px;height:20px;border:1px solid #ddd;border-radius:2px;font-size:6px;font-style:italic;color:#999;padding:6px 5px}
.search svg{position:absolute;right:5px;top:5px}
.btn-top{top:22px;width:45px;height:20px;border-radius:2px;color:#fff;font-size:6px;font-weight:600;text-align:center;line-height:20px}
.nav{left:102px;top:63px;width:506px;display:flex;justify-content:space-between;font-size:6px;font-weight:600;color:#222;text-transform:uppercase}
.tabs{left:95px;top:83px;width:517px;height:26px;display:flex}
.tab{flex:1;color:#fff;font-size:7px;font-weight:600;display:flex;align-items:center;justify-content:center;gap:4px;text-transform:uppercase}
.ico-c{width:6px;height:6px;border-radius:50%;border:1.5px solid #fff}
.strip{left:95px;top:110px;width:517px;height:23px;background:var(--gray);font-size:5.5px;font-style:italic;color:#777;padding:8px 10px}
.side{left:95px;top:142px;width:124px;height:236px;background:var(--yellow)}
.side h3{color:#fff;font-size:7.5px;font-weight:600;line-height:11px;padding:9px 10px 6px;border-bottom:1px solid rgba(255,255,255,.3);text-transform:uppercase}
.side ul{list-style:none;padding:5px 6px}
.side li{color:#fff;font-size:5.5px;height:16px;line-height:16px;white-space:nowrap}
.side li::before{content:"» "}
.results{left:95px;top:384px;width:123px;height:34px;background:var(--blue);border-radius:3px;color:#fff;font-size:13px;font-weight:700;display:flex;align-items:center;justify-content:center;gap:5px}
.results .ico-c{width:11px;height:11px;border-width:2px}
.find{left:225px;top:142px;width:387px;height:36px;background:var(--yellow);display:flex;align-items:center;padding:0 6px;gap:4px}
.find-label{color:#fff;font-size:7px;font-weight:600;line-height:10px;width:64px;text-transform:uppercase}
.field{height:21px;background:#fff;border-radius:2px;font-size:5.5px;font-style:italic;color:#999;padding:7px 5px;position:relative}
.field.sel::after{content:"";position:absolute;right:5px;top:9px;border:2.5px solid transparent;border-top-color:#666}
.find-btn{width:56px;height:21px;background:var(--yellow-dark);color:#fff;font-size:6.5px;text-align:center;line-height:21px;border:1px solid rgba(255,255,255,.4)}
.slider{left:225px;top:183px;width:387px;height:235px;background:linear-gradient(180deg,#dfe5e8 0%,#c9d3d6 35%,#7e9b5c 60%,#5f823f 100%)}
.arrows{left:225px;top:349px;display:flex}
.arrows span{width:22px;height:18px;background:var(--red);opacity:.85;color:#fff;font-size:9px;text-align:center;line-height:17px;border-right:1px solid rgba(255,255,255,.3)}
.caption{left:225px;top:374px;width:343px;height:44px;background:rgba(30,30,30,.85);color:#fff;padding:10px 14px}
.caption h2{font-size:10px;font-weight:600}
.caption p{font-size:6px;margin-top:3px}
.date{left:568px;top:374px;width:44px;height:44px;background:var(--red);color:#fff;text-align:center}
.date b{display:block;font-size:20px;line-height:27px;font-weight:600}
.date small{font-size:5px}
.sec-title{height:20px;border-bottom:1px solid var(--green)}
.sec-title span{display:inline-block;height:20px;color:#fff;font-size:8px;font-weight:700;padding:0 7px;line-height:20px;text-transform:uppercase}
.video-thumb{left:95px;top:463px;width:154px;height:111px;background:linear-gradient(180deg,#b8c7cf 0%,#8aa070 45%,#5c7d3c 100%)}
.play{left:160px;top:510px;width:24px;height:16px;background:var(--red);border-radius:4px}
.play::after{content:"";position:absolute;left:9px;top:4px;border:4px solid transparent;border-left:7px solid #fff}
.video-text{left:265px;top:465px;width:177px}
.video-text h3{font-size:8.5px;font-weight:600;color:#222}
.video-text p{font-size:5.3px;line-height:10.5px;color:var(--muted);margin-top:6px}
.video-text h4{font-size:7px;color:var(--red);font-weight:700;margin-top:6px}
.post{left:95px;width:346px;height:118px;border-bottom:1px solid var(--line)}
.post-img{position:absolute;left:0;top:0;width:119px;height:93px}
.post-tag{position:absolute;left:0;top:0;font-size:4px;color:#fff;padding:1px 3px;text-transform:uppercase}
.post-body{position:absolute;left:135px;top:8px;width:211px}
.post-body h3{font-size:8.5px;font-weight:600;color:#222}
.post-body p{font-size:5.3px;line-height:10.5px;color:var(--muted);margin-top:7px}
.meta{font-size:5.5px;color:#444;margin-top:6px;display:flex;align-items:center;gap:3px}
.meta a{color:var(--red);text-decoration:none;margin-left:4px}
.sq{width:7px;height:7px;border-radius:1px;display:inline-block}
.info{left:481px;width:131px;height:58px;border-bottom:1px solid var(--line)}
.info-img{position:absolute;left:0;top:0;width:48px;height:38px}
.info-body{position:absolute;left:54px;top:0;font-size:5.5px;line-height:9px;color:#333}
.stars{color:var(--yellow);font-size:5px;letter-spacing:1px}
.info-date{color:var(--red);font-size:5px}
.box{border:1px solid #ddd;background:#fff}
.partner-mark{width:100%;text-align:center;font-size:9px;font-weight:600;color:#1d3557;letter-spacing:.5px}
.contact-img{left:486px;top:846px;width:121px;height:96px;background:linear-gradient(180deg,#8fc4ea 0%,#cfe3f1 55%,#8db85a 75%,#6a9a3a 100%)}
.contact-text{left:486px;top:949px;font-size:6px;line-height:10.5px;color:#333}
.footer{left:0;top:1118px;width:707px;height:82px;background:var(--gray);border-top:1px solid #e2e2e2}
.social{left:292px;top:1133px;display:flex;gap:6px}
.social span{width:17px;height:17px;border-radius:2px}
.foot-line{width:707px;left:0;text-align:center;font-size:5.5px;color:#444;text-transform:uppercase}
.foot-copy{width:707px;left:0;top:1176px;text-align:center;font-size:5.5px;color:#555}
</style>
</head>
<body>
<div class="abs topbar"></div>

<header>
  <div class="abs brand"><span class="brand-dot"></span><span class="brand-name">Nordisk<br>Arbejdsidræt</span></div>
  <div class="abs search">Search
    <svg width="7" height="7" viewBox="0 0 10 10"><circle cx="4" cy="4" r="3" fill="none" stroke="#888" stroke-width="1.5"/><line x1="6.3" y1="6.3" x2="9" y2="9" stroke="#888" stroke-width="1.5"/></svg>
  </div>
  <div class="abs btn-top" style="left:518px;background:var(--red)">⊕ SIGN UP</div>
  <div class="abs btn-top" style="left:566px;background:var(--yellow)">⊕ TILMELD</div>
  <nav class="abs nav">
    <span>Om Nordisk Arbejdsidræt</span><span>Bliv medlem</span><span>Magasinet Arbejdsidræt</span><span>Find forening</span><span>Pressecenter Find person</span><span>Min side</span>
  </nav>
  <div class="abs tabs">
    <div class="tab" style="background:var(--green)"><span class="ico-c"></span>Idræt og motion</div>
    <div class="tab" style="background:var(--yellow)"><span class="ico-c"></span>Arrangementer og stævner</div>
    <div class="tab" style="background:var(--blue)"><span class="ico-c"></span>Sundhed på arbejdspladsen</div>
    <div class="tab" style="background:var(--red)"><span class="ico-c"></span>Foreningsnet</div>
  </div>
  <div class="abs strip">Find stævner og arrangementer f.eks. Arbejdsidræt Open, Cykel og Løb Stafetten, Vild Mandeløb og foreningsarrangementer</div>
</header>

<aside class="abs side">
  <h3>Arrangementer<br>og stævner</h3>
  <ul>
    <li>Arbejdsidræt Open</li><li>Cykel &amp; Løb Stafetten</li><li>Vild Mandeløb</li><li>Firmaernes Motionsdag 2015</li><li>Eventyrløb</li><li>Vennekamp</li><li>Vennebold</li><li>Pokal Fodbold</li><li>Pokal Håndbold</li><li>Onlineskydning</li><li>Gokart</li><li>Arkiv</li>
  </ul>
</aside>
<div class="abs results"><span class="ico-c"></span>RESULTATER</div>

<div class="abs find">
  <div class="find-label">Find<br>arrangement</div>
  <div class="field" style="width:83px">keyword</div>
  <div class="field sel" style="width:83px">Choose</div>
  <div class="field sel" style="width:83px">Choose</div>
  <div class="find-btn">⌕ SEARCH</div>
</div>
<div class="abs slider" role="img" aria-label="Golfers on a green fairway with bags and trolleys"></div>
<div class="abs arrows"><span>‹</span><span>›</span></div>
<div class="abs caption"><h2>VENNEKAMP 2015</h2><p>Danmarks sjoveste kollegaturnering i golf. Spil mod andre spillere på nye baner.</p></div>
<div class="abs date"><b>12</b><small>Dec</small></div>

<section>
  <div class="abs sec-title" style="left:95px;top:432px;width:346px"><span style="background:var(--green)">Our Video</span></div>
  <div class="abs video-thumb" role="img" aria-label="Video still of two golfers with bags on a course"></div>
  <div class="abs play"></div>
  <div class="abs video-text">
    <h3>Se video fra Vennekamp finalen 2011</h3>
    <p>Lorem ipsum dolor sit amet, consectetur adipiscing elit, sed do eiusmod tempor incididunt ut labore et dolore magna aliqua. Ut enim ad minim veniam.</p>
    <h4>Finalepræmier</h4>
    <p style="margin-top:3px">1. præmie: Et rejsegavekort på op til kr. 22.000,- pr. hold, dog max. kr. 5.500,- pr. tilmeldt spiller.<br>2. præmie: Et gavekort til golfudstyr på kr. 2000,- pr. hold.<br>3. præmie: Et gavekort til golfudstyr på kr. 1000,- pr. hold.</p>
  </div>
</section>

<section>
  <div class="abs sec-title" style="left:95px;top:596px;width:346px;border-color:var(--blue)"><span style="background:var(--blue)">Blog News</span></div>

  <article class="abs post" style="top:631px">
    <div class="post-img" role="img" aria-label="Two golfers on a putting green" style="background:linear-gradient(180deg,#6f8f4a,#4f7a2e)"></div>
    <span class="post-tag" style="background:var(--green)">Vennekamp 2016</span>
    <div class="post-body"><h3>Finalestævne fredag den 18. september 2015</h3>
      <p>Vinderne fra hver pulje kvalificerer sig til at deltage i finalestævnet, som spilles på Lindholt Golfklub, Engvej 12, 5491 Lindholt fredag den 18. september 2015 kl. 10.00.Finalen bliver spillet som stableford four-ball best-ball med 7/8 handicap og med gunstart.</p>
      <div class="meta">Posted on April 05 - 0 Comments - <a>Read More</a> <span class="sq" style="background:#3b5998"></span><span class="sq" style="background:#1da1f2"></span><span class="sq" style="background:#0077b5"></span></div></div>
  </article>

  <article class="abs post" style="top:749px">
    <div class="post-img" role="img" aria-label="Two golfers by a lake" style="background:linear-gradient(180deg,#9fb9c7,#5f8a45 60%,#4a6f33)"></div>
    <span class="post-tag" style="background:var(--blue)">Vennekamp 2016</span>
    <div class="post-body"><h3>Finalestævne fredag den 18. september 2015</h3>
      <p>Vinderne fra hver pulje kvalificerer sig til at deltage i finalestævnet, som spilles på Lindholt Golfklub, Engvej 12, 5491 Lindholt fredag den 18. september 2015 kl. 10.00.Finalen bliver spillet som stableford four-ball best-ball med 7/8 handicap og med gunstart.</p>
      <div class="meta">Posted on April 05 - 0 Comments - <a>Read More</a> <span class="sq" style="background:#3b5998"></span><span class="sq" style="background:#1da1f2"></span><span class="sq" style="background:#0077b5"></span></div></div>
  </article>

  <article class="abs post" style="top:867px">
    <div class="post-img" role="img" aria-label="Couple walking with golf bags" style="background:linear-gradient(180deg,#8cc3e8,#c7dcc0 55%,#7fae4a)"></div>
    <span class="post-tag" style="background:var(--yellow)">Vennekamp 2016</span>
    <div class="post-body"><h3>Finalestævne fredag den 18. september 2015</h3>
      <p>Vinderne fra hver pulje kvalificerer sig til at deltage i finalestævnet, som spilles på Lindholt Golfklub, Engvej 12, 5491 Lindholt fredag den 18. september 2015 kl. 10.00.Finalen bliver spillet som stableford four-ball best-ball med 7/8 handicap og med gunstart.</p>
      <div class="meta">Posted on April 05 - 0 Comments - <a>Read More</a> <span class="sq" style="background:#3b5998"></span><span class="sq" style="background:#1da1f2"></span><span class="sq" style="background:#0077b5"></span></div></div>
  </article>

  <article class="abs post" style="top:986px;border:0">
    <div class="post-img" role="img" aria-label="Golf green at sunset" style="background:linear-gradient(180deg,#f2d27a,#b9b24a 45%,#5e8a2a)"></div>
    <span class="post-tag" style="background:var(--red)">Vennekamp 2016</span>
    <div class="post-body"><h3>Finalestævne fredag den 18. september 2015</h3>
      <p>Vinderne fra hver pulje kvalificerer sig til at deltage i finalestævnet, som spilles på Lindholt Golfklub, Engvej 12, 5491 Lindholt fredag den 18. september 2015 kl. 10.00.Finalen bliver spillet som stableford four-ball best-ball med 7/8 handicap og med gunstart.</p>
      <div class="meta">Posted on April 05 - 0 Comments - <a>Read More</a> <span class="sq" style="background:#3b5998"></span><span class="sq" style="background:#1da1f2"></span><span class="sq" style="background:#0077b5"></span></div></div>
  </article>
</section>

<aside>
  <div class="abs sec-title" style="left:481px;top:433px;width:131px;border-color:var(--red)"><span style="background:var(--red)">Information</span></div>
  <div class="abs info" style="top:462px"><div class="info-img" role="img" aria-label="Golf ball on tee" style="background:linear-gradient(180deg,#d9e4c8,#6f9a3c)"></div>
    <div class="info-body">Turneringen er åben foalle<br>klubgolfere med gyldigt<br><span class="stars">★★★★★</span><br><span class="info-date">12 MARCH 2015</span></div></div>
  <div class="abs info" style="top:520px"><div class="info-img" role="img" aria-label="Golfer on fairway" style="background:linear-gradient(180deg,#a8a86a,#5d7a2c)"></div>
    <div class="info-body">Turneringen er åben foalle<br>klubgolfere med gyldigt<br><span class="stars">★★★★★</span><br><span class="info-date">12 MARCH 2015</span></div></div>
  <div class="abs info" style="top:578px"><div class="info-img" role="img" aria-label="Golfer swinging" style="background:linear-gradient(180deg,#d8c89a,#8aa35a)"></div>
    <div class="info-body">Turneringen er åben foalle<br>klubgolfere med gyldigt<br><span class="stars">★★★★★</span><br><span class="info-date">12 MARCH 2015</span></div></div>

  <div class="abs sec-title" style="left:481px;top:642px;width:131px;border-color:var(--blue)"><span style="background:var(--blue)">Partner</span></div>
  <div class="abs box" style="left:481px;top:674px;width:131px;height:124px">
    <div style="font-size:4.5px;color:#333;margin:13px 0 0 17px">I samarbejde med:</div>
    <div class="partner-mark" style="margin-top:3px">NORDGOLF UNION</div>
    <div style="width:26px;height:26px;border-radius:50%;background:#d9dde6;margin:14px auto 6px"></div>
    <div class="partner-mark" style="font-size:12px">FJORD REJSER</div>
  </div>

  <div class="abs sec-title" style="left:481px;top:808px;width:131px;border-color:var(--yellow)"><span style="background:var(--yellow)">Contact</span></div>
  <div class="abs box" style="left:481px;top:840px;width:131px;height:155px"></div>
  <div class="abs contact-img" role="img" aria-label="Golfer mid-swing against blue sky"></div>
  <div class="abs contact-text">Mads Holmgaard<br>Generalsekretær<br>Tlf: 41 22 80 10<br>Mail: mh@arbejdsidraet.dk</div>
</aside>

<footer>
  <div class="abs footer"></div>
  <div class="abs social" aria-label="Social links">
    <span style="background:#2d4e8a"></span><span style="background:#1d8fd6"></span><span style="background:#c8232c"></span><span style="background:#c4302b"></span><span style="background:#6b4c3b"></span><span style="background:#e8632a"></span>
  </div>
  <div class="abs foot-line" style="top:1162px">Nordisk Arbejdsidræt Havnegade 24 5700 Svendborg Tlf. 62 20 14 40 , kontakt@arbejdsidraet.dk</div>
  <div class="abs foot-copy">© 2015 all copyrights are reserved. &nbsp;- &nbsp;Advertise &nbsp;- &nbsp;Terms &nbsp;- &nbsp;Feedback &nbsp;Links</div>
</footer>
</body>
</html>
```